Social Media Graphics - Oakline Push REVISED

Create 6-7 individual social media graphics (square size) to encourage folks to join our online course called:

The Harvest Ledger Circle
How to Launch a Multi-Million Business From Scratch
Sign Up Today!

IMPORTANT: Make the largest and most prominent text on the graphic be: How to Launch a Multi-Million Business From Scratch

For the color scheme of the graphics, let's try a blue color palette; make sure the graphics appeal to both men and women

Make sure each graphic contains 1 of the 3 pics attached (crop pic as needed); and make sure one of the graphics is all TEXT only.

Target Market(s)

men and women looking to start a business

Industry/Entity Type

Entrepreneurship

Colors
0054AA
0677BA
7BADD7
CADEEF
E8F1F8

Requirements
Must have
• All the text and use the 3 pics provided; one graphic can be all text; Simple, modern design that's easy to read

```html
<!DOCTYPE html>
<html lang="en">
<head>
<meta charset="utf-8">
<title>Social Media Ads – The Harvest Ledger Circle</title>
<link rel="stylesheet" href="https://fonts.googleapis.com/css2?family=Anton&family=Open+Sans:wght@400&family=Oswald:wght@700&display=swap">
<style>
  :root {
    --page-bg: #ffffff;
    --label-ink: #111111;
    --blue-deep: #0054aa;
    --blue-mid: #0677ba;
    --blue-bright: #0a5cff;
    --blue-light: #7badd7;
    --blue-pale: #cadeef;
    --navy-type: #1d3550;
    --gold: #e3b83a;
    --gold-dark: #9a6a10;
    --gold-glow: #ffd86a;
    --night: #140d05;
    --white: #ffffff;
  }
  * { margin: 0; padding: 0; box-sizing: border-box; }
  html, body { width: 1200px; height: 849px; overflow: hidden; background: var(--page-bg); }
  body { position: relative; font-family: "Open Sans", Arial, sans-serif; }

  .ad-block { position: absolute; top: 208px; width: 362px; }
  .ad-block--one { left: 30px; }
  .ad-block--two { left: 418px; }
  .ad-block--three { left: 806px; }

  .ad-label {
    height: 30px; text-align: center;
    font-size: 16.5px; color: var(--label-ink); line-height: 30px;
  }
  .ad {
    position: relative; margin-top: 5px; width: 362px; height: 362px; overflow: hidden;
    background: var(--night);
  }
  .ad-backdrop {
    position: absolute; inset: 0;
    background:
      radial-gradient(circle at 70% 55%, rgba(255,216,106,.55), transparent 45%),
      radial-gradient(circle at 30% 40%, rgba(227,184,58,.45), transparent 40%),
      linear-gradient(180deg, #1a1005 0%, #6b4a10 35%, #b8871f 60%, #5a3a0a 85%, #1a1005 100%);
  }
  .host-photo { position: absolute; bottom: 0; border-radius: 90px 90px 0 0; }
  .host-photo--dark { background: linear-gradient(180deg, #3a2a22 0%, #1d1f24 40%, #15171b 100%); }
  .host-photo--denim { background: linear-gradient(180deg, #3b2a22 0%, #2a4466 45%, #1f3a5e 100%); }
  .host-photo--rose { background: linear-gradient(180deg, #3a261f 0%, #c84a62 45%, #b43e57 100%); }
  .host-photo--black { background: linear-gradient(180deg, #3a2a22 0%, #222 40%, #161616 100%); }

  .ribbon { position: absolute; inset: 0; width: 362px; height: 362px; }
  .ribbon-text { font-family: "Oswald", Arial, sans-serif; font-weight: 700; font-size: 15px; fill: var(--white); }

  .headline {
    position: absolute; left: 0; right: 0; text-align: center;
    font-family: "Anton", Impact, sans-serif; color: var(--navy-type); line-height: 1;
  }
  .headline span { display: block; }
  .headline .line-small {
    font-size: 34px; letter-spacing: -0.5px;
    color: #2a3d52;
    text-shadow: -1px -1px 0 var(--white), 1px -1px 0 var(--white), -1px 1px 0 var(--white), 1px 1px 0 var(--white), 0 3px 0 #9fb3c7, 0 4px 4px rgba(0,0,0,.6);
  }
  .headline .line-mid {
    font-size: 38px; margin-top: 6px;
    text-shadow: -1px -1px 0 var(--gold-glow), 1px -1px 0 var(--gold-glow), -1px 1px 0 var(--gold-glow), 1px 1px 0 var(--gold-glow), 0 3px 0 var(--gold-dark), 0 5px 5px rgba(0,0,0,.6);
  }
  .headline .line-big {
    font-size: 58px; letter-spacing: 1px; margin-top: 4px;
    text-shadow: -1.5px -1.5px 0 var(--gold-glow), 1.5px -1.5px 0 var(--gold-glow), -1.5px 1.5px 0 var(--gold-glow), 1.5px 1.5px 0 var(--gold-glow), 0 4px 0 var(--gold-dark), 0 7px 6px rgba(0,0,0,.6);
  }
  .headline .line-small--last { margin-top: 6px; }
  .headline--low { top: 138px; }
  .headline--high { top: 118px; }

  .cta {
    position: absolute; left: 72px; width: 214px; bottom: 0; height: 23px;
    background: linear-gradient(180deg, var(--blue-bright), var(--blue-deep));
    border-radius: 10px 10px 0 0;
    text-align: center; line-height: 23px;
    font-family: "Oswald", Arial, sans-serif; font-weight: 700; font-size: 12.5px; letter-spacing: .5px;
    color: var(--white);
  }
</style>
</head>
<body>

<section class="ad-block ad-block--one">
  <p class="ad-label">Social Media AD 1200x1200px</p>
  <div class="ad">
    <div class="ad-backdrop" role="img" aria-label="Stacks of gold coins and bars with sparkling lights on a dark background"></div>
    <div class="host-photo host-photo--dark" style="left:0;width:190px;height:340px;" role="img" aria-label="Photo of the male course host in a black turtleneck"></div>
    <div class="host-photo host-photo--denim" style="left:175px;width:187px;height:310px;" role="img" aria-label="Photo of the female course host in a denim jacket"></div>
    <svg class="ribbon" viewBox="0 0 362 362" aria-hidden="false">
      <polygon points="200,0 250,0 362,104 362,162" fill="#0a5cff"/>
      <text class="ribbon-text" x="0" y="0" text-anchor="middle" transform="translate(290,72) rotate(44)">The Harvest Ledger Circle</text>
    </svg>
    <h2 class="headline headline--low">
      <span class="line-small">How to Launch</span>
      <span class="line-mid">a Multi-Million</span>
      <span class="line-big">BUSINESS</span>
      <span class="line-small line-small--last">From Scratch</span>
    </h2>
    <div class="cta">SIGN UP TODAY!</div>
  </div>
</section>

<section class="ad-block ad-block--two">
  <p class="ad-label">Social Media AD 1200x1200px</p>
  <div class="ad">
    <div class="ad-backdrop" role="img" aria-label="Stacks of gold coins and bars with sparkling lights on a dark background"></div>
    <div class="host-photo host-photo--rose" style="left:0;width:170px;height:335px;" role="img" aria-label="Photo of the female course host in a pink dress"></div>
    <div class="host-photo host-photo--black" style="left:150px;width:170px;height:340px;" role="img" aria-label="Photo of the male course host in a black jacket"></div>
    <svg class="ribbon" viewBox="0 0 362 362">
      <polygon points="200,0 250,0 362,104 362,162" fill="#0a5cff"/>
      <text class="ribbon-text" x="0" y="0" text-anchor="middle" transform="translate(290,72) rotate(44)">The Harvest Ledger Circle</text>
    </svg>
    <h2 class="headline headline--low">
      <span class="line-small">How to Launch</span>
      <span class="line-mid">a Multi-Million</span>
      <span class="line-big">BUSINESS</span>
      <span class="line-small line-small--last">From Scratch</span>
    </h2>
    <div class="cta">SIGN UP TODAY!</div>
  </div>
</section>

<section class="ad-block ad-block--three">
  <p class="ad-label">Social Media AD 1200x1200px</p>
  <div class="ad">
    <div class="ad-backdrop" role="img" aria-label="Stacks of gold coins and bars with sparkling lights on a dark background"></div>
    <svg class="ribbon" viewBox="0 0 362 362">
      <polygon points="200,0 250,0 362,104 362,162" fill="#0a5cff"/>
      <text class="ribbon-text" x="0" y="0" text-anchor="middle" transform="translate(290,72) rotate(44)">The Harvest Ledger Circle</text>
    </svg>
    <h2 class="headline headline--high">
      <span class="line-small">How to Launch</span>
      <span class="line-mid">a Multi-Million</span>
      <span class="line-big">BUSINESS</span>
      <span class="line-small line-small--last">From Scratch</span>
    </h2>
    <div class="cta">SIGN UP TODAY!</div>
  </div>
</section>

</body>
</html>
```